Hemp company needs website/online store

We are a startup hemp company and we need an online storefront designed. We are very open do design, but will include our logo to help. We make 100% hemp derived products like edibles, concentrates, vapes and THCA flower. Everything is grown locally, and all products are extracted and made in house.

• I would like to highlight that we have Cannabis products that are hemp derived and 100% legal across the US. Also that all cannabis is locally grown and products are extracted and made in house and sent out for third party lab testing.

```html
<!DOCTYPE html>
<html lang="en">
<head>
<meta charset="utf-8">
<title>Sunleaf Hemp</title>
<link href="https://fonts.googleapis.com/css2?family=Exo+2:wght@400;500;600;700;800&display=swap" rel="stylesheet">
<style>
:root{
  --green:#4b7a2f;
  --green-bg:#3f7630;
  --green-dark:#3a7429;
  --lime:#8cae2b;
  --ink:#111;
  --grey-bg:#f3f3f3;
  --star:#f39a14;
  --muted:#aaa;
  --white:#fff;
  --footer:#000;
}
*{margin:0;padding:0;box-sizing:border-box}
html,body{width:1200px;height:2994px;overflow:hidden}
body{position:relative;font-family:"Exo 2",sans-serif;color:var(--ink);background:var(--white)}
.abs{position:absolute}
.topbar{left:0;top:0;width:1200px;height:31px;background:var(--green);color:var(--white);font-size:12px}
.topbar .mail{left:99px;top:8px;display:flex;align-items:center;gap:6px}
.topbar .ship{left:0;width:1200px;top:8px;text-align:center;font-weight:500;padding-left:105px}
.topbar .icons{left:1060px;top:9px;display:flex;gap:14px}
.header{left:0;top:31px;width:1200px;height:107px;background:var(--white)}
.brand{left:99px;top:33px;display:flex;align-items:center;gap:10px;font-size:30px;font-weight:700;color:var(--lime)}
.brand .mark{width:22px;height:22px;background:var(--green)}
.nav a{position:absolute;top:42px;font-size:15px;color:#222;text-decoration:none;transform:translateX(-50%);white-space:nowrap}
.nav .leaf{position:absolute;left:549px;top:62px}
.hero{left:0;top:138px;width:1200px;height:562px;background:linear-gradient(90deg,#0d130b 0%,#1f3419 35%,#4f6b45 60%,#a9b8a7 75%,#5f8a45 100%)}
.hero h2{position:absolute;left:99px;top:130px;font-size:36px;font-weight:400;color:var(--white);letter-spacing:.5px}
.hero h1{position:absolute;left:99px;top:175px;font-size:53px;font-weight:800;color:var(--white)}
.hero p{position:absolute;left:100px;top:246px;width:420px;font-size:15.5px;line-height:26px;color:var(--white)}
.btn{position:absolute;display:flex;align-items:center;justify-content:center;gap:18px;color:var(--white);font-size:17px;font-weight:500;height:48px;width:170px}
.hero .btn{left:99px;top:324px;background:var(--lime)}
.down{left:565px;top:665px;width:70px;height:70px;border-radius:50%;background:var(--white);z-index:3;display:flex;align-items:center;justify-content:center}
.cats{left:0;top:700px;width:1200px;height:611px;background:radial-gradient(ellipse at 50% 40%,#4a8338 0%,var(--green-bg) 70%)}
.title{position:absolute;left:0;width:1200px;text-align:center;font-weight:800}
.sub{position:absolute;left:0;width:1200px;text-align:center;font-size:17px}
.cats .title{top:92px;font-size:41px;color:var(--white)}
.cats .sub{top:161px;color:var(--white)}
.cat{position:absolute;top:223px;width:242px;height:241px}
.cat .label{position:absolute;left:21px;top:220px;width:199px;height:51px;background:var(--white);color:var(--green);font-size:20px;font-weight:700;display:flex;align-items:center;justify-content:center}
.products{left:0;top:1311px;width:1200px;height:745px;background:var(--grey-bg)}
.products .title{top:100px;font-size:43px}
.products .sub{top:170px}
.prod{position:absolute;top:245px;width:228px}
.prod .card{height:311px;background:var(--white);position:relative}
.prod .pic{position:absolute;left:24px;top:70px;width:180px;height:150px;border-radius:8px}
.prod .stars{margin-top:20px;display:flex;gap:4px;color:var(--star);font-size:17px;letter-spacing:1px}
.prod h3{margin-top:8px;font-size:22px;font-weight:400}
.prod .price{margin-top:10px;font-size:16px}
.prod .price s{color:var(--muted);margin-right:8px}
.tool{position:absolute;right:10px;width:36px;height:36px;border-radius:50%;display:flex;align-items:center;justify-content:center;background:#ddd}
.badge{position:absolute;right:14px;top:265px;background:#8cc63f;color:var(--white);font-size:14px;padding:3px 10px}
.feature{left:0;top:2056px;width:1200px;height:528px;background:linear-gradient(90deg,#5a3a20 0%,#9a6a3c 25%,#c8a67a 45%,#8d6a45 70%,#4a2f1b 100%)}
.feature .box{position:absolute;left:617px;top:88px;width:483px;height:349px;background:var(--white);border-radius:4px}
.feature h2{position:absolute;left:27px;top:28px;font-size:40px;font-weight:700;line-height:53px}
.feature p{position:absolute;left:28px;top:147px;width:405px;font-size:14.5px;line-height:23px;color:#555}
.feature .btn{left:27px;top:278px;background:var(--green-dark)}
.footer{left:0;top:2584px;width:1200px;height:410px;background:var(--footer);color:var(--white)}
.footer .fbrand{position:absolute;left:96px;top:152px;width:300px;font-size:36px;font-weight:700;color:var(--lime);display:flex;align-items:center;gap:12px;white-space:nowrap}
.footer .fbrand .mark{width:26px;height:26px;background:var(--green);flex:none}
.col{position:absolute;top:72px}
.col h4{font-size:19px;font-weight:700;letter-spacing:.3px}
.col ul{list-style:none;margin-top:26px}
.col li{font-size:15px;height:28.4px}
.loc{position:absolute;left:818px;display:flex;align-items:flex-start;gap:17px;font-size:15px;line-height:24px}
.loc .ic{width:36px;height:36px;border-radius:50%;border:2px solid var(--white);flex:none;display:flex;align-items:center;justify-content:center}
.social{position:absolute;top:270px;width:40px;height:40px;border-radius:50%}
.rule{left:114px;top:321px;width:977px;height:1px;background:#666}
.copy{position:absolute;left:0;width:1200px;top:342px;text-align:center;font-size:15px}
</style>
</head>
<body>
<div class="abs topbar">
  <div class="abs mail"><svg width="12" height="10" viewBox="0 0 12 10"><rect x=".5" y=".5" width="11" height="9" fill="none" stroke="#fff"/><path d="M.5 .5 6 5.5 11.5 .5" fill="none" stroke="#fff"/></svg>info@sunleafhemp.com</div>
  <div class="abs ship">Free Shipping on All Orders Over 75$</div>
  <div class="abs icons">
    <svg width="11" height="11" viewBox="0 0 11 11"><circle cx="5.5" cy="3" r="2.6" fill="#fff"/><path d="M1 11c0-4 9-4 9 0z" fill="#fff"/></svg>
    <svg width="12" height="11" viewBox="0 0 12 11"><path d="M0 1h2l2 6h6l2-5H3" fill="#fff"/><circle cx="4.5" cy="9.5" r="1.2" fill="#fff"/><circle cx="9.5" cy="9.5" r="1.2" fill="#fff"/></svg>
  </div>
</div>

<header class="abs header">
  <div class="abs brand"><span class="mark"></span>Sunleaf Hemp</div>
  <nav class="nav">
    <a style="left:558px">Home</a>
    <svg class="leaf" width="20" height="16" viewBox="0 0 20 16"><path d="M10 0 8 10 10 14 12 10ZM0 6l9 8-4-6ZM20 6l-9 8 4-6Z" fill="#8cae2b"/></svg>
    <a style="left:675px">About Us</a>
    <a style="left:818px">Our Products</a>
    <a style="left:944px">Blog</a>
    <a style="left:1063px">Contact Us</a>
  </nav>
</header>

<section class="abs hero" role="img" aria-label="Scientist in lab goggles and mask inspecting hemp plants in a greenhouse">
  <h2>WELCOME TO</h2>
  <h1>SUNLEAF HEMP</h1>
  <p>Cannabis products that are hemp derived and 100% legal across the US</p>
  <a class="btn">Shop Now <svg width="8" height="12" viewBox="0 0 8 12"><path d="M2 1l5 5-5 5" fill="none" stroke="#fff" stroke-width="1.8"/></svg></a>
</section>

<div class="abs down"><svg width="20" height="34" viewBox="0 0 20 34"><path d="M10 2v28M3 22l7 9 7-9" fill="none" stroke="#3f7630" stroke-width="4"/></svg></div>

<section class="abs cats">
  <h2 class="title">SHOP BY CATEGORIES</h2>
  <p class="sub">Lorem ipsum dolor sit amet, consectetur adipiscing elit, sed do eiusmod tempor incididunt</p>
  <div class="cat" style="left:99px"><div role="img" aria-label="Gloved hand writing notes among hemp plants" style="height:241px;background:linear-gradient(135deg,#2f4a2a,#6a8a5e,#2a3b2c)"></div><div class="label">Magna Aliqua</div></div>
  <div class="cat" style="left:352px"><div role="img" aria-label="Hemp oil in glass jars with seeds and leaves" style="height:241px;background:linear-gradient(135deg,#4a5a2a,#b9c24a,#3b3a30)"></div><div class="label">Magna Aliqua</div></div>
  <div class="cat" style="left:605px"><div role="img" aria-label="Woman holding a small jar of hemp flower" style="height:241px;background:linear-gradient(135deg,#7a8068,#6b4a38,#3a3a34)"></div><div class="label">Magna Aliqua</div></div>
  <div class="cat" style="left:859px"><div role="img" aria-label="Tincture bottle and dropper beside hemp buds on burlap" style="height:241px;background:linear-gradient(135deg,#8a5a30,#a98a60,#6a4a28)"></div><div class="label">Magna Aliqua</div></div>
</section>

<section class="abs products">
  <h2 class="title">OUR PRODUCTS</h2>
  <p class="sub">Lorem ipsum dolor sit amet, consectetur adipiscing elit, sed do eiusmod tempor incididunt</p>

  <div class="prod" style="left:98px">
    <div class="card"><div class="pic" role="img" aria-label="Hemp buds with green gummies in a glass bowl" style="background:radial-gradient(#8ec24a,#7f8a4a 45%,#fff 72%)"></div></div>
    <div class="stars">★★★★☆</div>
    <h3>Edibles</h3>
    <div class="price"><s>£170.00</s>£111.00</div>
  </div>

  <div class="prod" style="left:355px">
    <div class="card" style="box-shadow:0 2px 10px rgba(0,0,0,.12)">
      <div class="pic" role="img" aria-label="Amber tincture bottles with a hemp leaf" style="background:radial-gradient(#7a4a20,#4a6a2a 45%,#fff 72%)"></div>
      <div class="tool" style="top:12px;background:var(--lime)"><svg width="16" height="14" viewBox="0 0 16 14"><path d="M8 13 1.5 6.5A3.5 3.5 0 0 1 8 2.5a3.5 3.5 0 0 1 6.5 4Z" fill="none" stroke="#fff" stroke-width="1.5"/></svg></div>
      <div class="tool" style="top:56px"><svg width="16" height="16" viewBox="0 0 16 16"><circle cx="6.5" cy="6.5" r="4.5" fill="none" stroke="#111" stroke-width="2"/><path d="M10 10l5 5" stroke="#111" stroke-width="2.5"/></svg></div>
      <div class="tool" style="top:102px"><svg width="16" height="10" viewBox="0 0 16 10"><path d="M1 5c4-6 10-6 14 0-4 6-10 6-14 0Z" fill="#111"/><circle cx="8" cy="5" r="2" fill="#ddd"/></svg></div>
      <div class="badge">-19%</div>
    </div>
    <div class="stars">★★★★☆</div>
    <h3>Concentrates</h3>
    <div class="price"><s>£170.00</s>£111.00</div>
  </div>

  <div class="prod" style="left:612px">
    <div class="card"><div class="pic" role="img" aria-label="Row of vape pens and e-liquid bottles" style="background:radial-gradient(#6a7a9a,#c24a4a 40%,#fff 72%)"></div></div>
    <div class="stars">★★★★☆</div>
    <h3>Vapes</h3>
    <div class="price"><s>£170.00</s>£111.00</div>
  </div>

  <div class="prod" style="left:869px">
    <div class="card"><div class="pic" role="img" aria-label="Single dried hemp flower bud" style="background:radial-gradient(#6a6a4a,#7a6a4a 40%,#fff 70%)"></div></div>
    <div class="stars">★★★★☆</div>
    <h3>THCA Flowers</h3>
    <div class="price"><s>£170.00</s>£111.00</div>
  </div>
</section>

<section class="abs feature" role="img" aria-label="Amber tincture bottle with dropper and hemp buds in a burlap sack">
  <div class="box">
    <h2>We Provide You<br>The Best Products</h2>
    <p>Lorem ipsum dolor sit amet, consectetur adipiscing elit, sed do eiusmod tempor incididunt ut labore et dolore magna aliqua. Ut enim ad minim veniam, quis nostrud exercitation ullamco laboris nisi ut aliquip ex ea commodo consequat.</p>
    <a class="btn">Read More <svg width="8" height="12" viewBox="0 0 8 12"><path d="M2 1l5 5-5 5" fill="none" stroke="#fff" stroke-width="1.8"/></svg></a>
  </div>
</section>

<footer class="abs footer">
  <div class="fbrand"><span class="mark"></span>Sunleaf Hemp</div>
  <div class="col" style="left:428px"><h4>NAVIGATION</h4><ul><li>Home</li><li>About Us</li><li>Our Products</li><li>Blog</li><li>Contact Us</li></ul></div>
  <div class="col" style="left:620px"><h4>QUICK LINKS</h4><ul><li>Terms &amp; Conditions</li><li>Privacy Policy</li><li>About Us</li><li>Support</li></ul></div>
  <div class="col" style="left:818px"><h4>OUR LOCATION</h4></div>
  <div class="loc" style="top:124px"><span class="ic"><svg width="14" height="18" viewBox="0 0 14 18"><path d="M7 17C2 11 1 9 1 7a6 6 0 0 1 12 0c0 2-1 4-6 10Z" fill="none" stroke="#fff" stroke-width="1.6"/><circle cx="7" cy="7" r="2" fill="#fff"/></svg></span><span>115475&nbsp; Duis aute irure dolor in<br>reprehenderit</span></div>
  <div class="loc" style="top:189px"><span class="ic"><svg width="16" height="16" viewBox="0 0 16 16"><path d="M3 1l3 3-2 2c1 2 3 4 5 5l2-2 3 3-2 3C7 15 1 9 1 3Z" fill="none" stroke="#fff" stroke-width="1.5"/></svg></span><span style="padding-top:6px">+1 555 014 2288</span></div>
  <div class="loc" style="top:245px"><span class="ic"><svg width="16" height="12" viewBox="0 0 16 12"><rect x="1" y="1" width="14" height="10" rx="1" fill="none" stroke="#fff" stroke-width="1.4"/><path d="M1 1l7 6 7-6" fill="none" stroke="#fff" stroke-width="1.4"/></svg></span><span style="padding-top:6px">info@sunleafhemp.com</span></div>
  <span class="social" style="left:117px;background:var(--lime)"></span>
  <span class="social" style="left:168px;border:1px solid #444"></span>
  <span class="social" style="left:216px;border:1px solid #444"></span>
  <div class="abs rule"></div>
  <p class="copy">© copyrights 2023 Sunleaf Hemp | &nbsp;All Rights Reserved</p>
</footer>
</body>
</html>
```